Local fast-growing company in the service sector

We are looking for a modern business card design, which should also appear on our letterheads

Target Market(s)

Private and industrial sectors

Contact Information for Business Card

Vorname Name
Kellberger Str. 18
74215 Lindenfeld
Tel.: 07146-839214-0
Name@agentur-kvtl.de

Colors
9d9d9d
919191
aaaaaa

Requirements
Must have
• The logo (file) in silver

```html
<!DOCTYPE html>
<html lang="de">
<head>
<meta charset="utf-8">
<title>KVTL – Visitenkarte</title>
<link href="https://fonts.googleapis.com/css2?family=Lato:wght@400;700&display=swap" rel="stylesheet">
<style>
  :root {
    --backdrop: #e6e3df;
    --card: #2a2d31;
    --silver-light: #d4d4d4;
    --silver: #aaaaaa;
    --silver-mid: #9d9d9d;
    --silver-dark: #919191;
  }
  html, body {
    margin: 0;
    padding: 0;
    width: 1200px;
    height: 902px;
    overflow: hidden;
    background: var(--backdrop);
    font-family: "Lato", Arial, sans-serif;
  }
  .business-card {
    position: absolute;
    left: 100px;
    top: 166px;
    width: 1000px;
    height: 570px;
    background: var(--card);
    box-shadow: 0 10px 30px rgba(0,0,0,0.18);
  }
  .brand {
    position: absolute;
    left: 72px;
    top: 236px;
    display: flex;
    align-items: center;
    gap: 22px;
  }
  .brand-mark {
    width: 64px;
    height: 64px;
    border-radius: 50%;
    background: var(--silver);
  }
  .brand-name {
    font-weight: 700;
    font-size: 86px;
    line-height: 1;
    color: var(--silver);
    letter-spacing: 4px;
  }
  .divider {
    position: absolute;
    left: 499px;
    top: 171px;
    width: 2px;
    height: 234px;
    background: var(--silver-dark);
    opacity: 0.7;
  }
  .contact {
    position: absolute;
    left: 550px;
    top: 172px;
    color: var(--silver);
  }
  .contact-name {
    margin: 0 0 32px;
    font-weight: 700;
    font-size: 34px;
    letter-spacing: 0.5px;
    color: var(--silver-light);
  }
  .contact-address {
    margin: 0 0 14px;
    font-size: 25px;
    line-height: 34px;
    font-style: normal;
    color: var(--silver-mid);
  }
  .contact-line {
    display: flex;
    align-items: center;
    gap: 10px;
    font-size: 25px;
    line-height: 34px;
    color: var(--silver);
  }
  .contact-icon {
    width: 30px;
    height: 30px;
    flex: none;
  }
</style>
</head>
<body>
  <div class="business-card">
    <div class="brand">
      <span class="brand-mark"></span>
      <span class="brand-name">KVTL</span>
    </div>

    <div class="divider"></div>

    <div class="contact">
      <h1 class="contact-name">LUKAS BRENNER</h1>
      <address class="contact-address">Kellberger Str. 18<br>74215 Lindenfeld</address>
      <div class="contact-line">
        <svg class="contact-icon" viewBox="0 0 30 30" aria-hidden="true">
          <circle cx="15" cy="15" r="13" fill="none" stroke="#aaaaaa" stroke-width="2"/>
          <path d="M8 12 q7 -6 14 0 l-2 2.5 -2.5 -1 v-1.5 h-5 v1.5 l-2.5 1z" fill="#aaaaaa"/>
          <rect x="9.5" y="14.5" width="11" height="6.5" rx="1" fill="#aaaaaa"/>
        </svg>
        <span>07146-839214-0</span>
      </div>
      <div class="contact-line">
        <svg class="contact-icon" viewBox="0 0 30 30" aria-hidden="true">
          <circle cx="15" cy="15" r="13" fill="none" stroke="#aaaaaa" stroke-width="2"/>
          <rect x="8" y="10" width="14" height="10" rx="1" fill="#aaaaaa"/>
          <path d="M8.5 10.5 L15 16 L21.5 10.5" fill="none" stroke="#2a2d31" stroke-width="1.5"/>
        </svg>
        <span>Name@agentur-kvtl.de</span>
      </div>
    </div>
  </div>
</body>
</html>
```